Wordpress Theme for Northway Clinics

** Please view updated Sitemap2.pdf doc to clarify some confusion ***

This is a multiuser WordPress subscription site for Northway Clinics. Please see attachment for sitemap. Please do not include extra content like social media icons, search bars, or images. If you have questions, please ask for clarification.
The site contains the following pages and sub-pages:

1. Home
2. Our Clinic
2a. Our Clinic > Mission
2b. Our Clinic > Services
2c. Our Clinic > Clinic Policies
2d. Our Clinic > Schedules
3. Our Staff
3a. Our Staff > [Staff member page]
4. Resources
4a. Resources > Patient Health (index)
4b. Resources > Patient Health (index) > [post]
4c. Resources > Links
4d. Resources > Forms
5. Alerts
5a. Alerts > [Alert Page]
6. Contact Us

Includes the Following Pages, Subpages, and Content
1. Home
a. About Us
b. Our Staff
c. Bulletins
d. Accepting New Patients (shown as an alert widget)
e. Links
i. Physician Toolbox
ii. Book an Appointment
f. Clinic Policies
i. Show first 3 policies (e.g. Late Arrivals, Missed Appointments, Fees)
ii. Link to Clinic Policies page
g. Primary widget (displayed on all pages)
i. Hours of operation
ii. Contact Info
1. Tel
2. Fax
3. Email
4. Address
5. Get directions (link to Google Maps)
2. Our Clinic
a. Main Page
i. Clinic Name
ii. Overview
iii. Languages Spoken
iv. Secondary Navigation
1. Mission
2. Services
3. Clinic Policies
4. Schedules (see attachment)
b. Our Clinic > Mission
c. Our Clinic > Services
i. For each service include service TITLE and DESCRIPTION
d. Our Clinic > Clinic Policies
i. For each policy include policy TITLE and DESCRIPTION
ii. Include the following policies in mockup
1. Late arrivals
2. Missed appointments
3. Fees for missed appointments
4. Referrals and follow-ups
5. Services not covered by RDA
6. Information for LTF patients
7. Medical Legal Reports
e. Our Clinic > Schedules
3. Our Staff
a. Main Page
i. Display a list of staff members. Include NAME and DESIGNATION
b. Our Staff > [Staff Name]
i. Include NAME, PICTURE, DESIGNATION, and BIO
4. Resources
a. Resources > Patient Health
i. Main Page
1. Posts (ordered by date)
a. Title
b. Summary
2. Side Navigation
a. Post Categories
ii. Patient Health > [post title]
1. Title
2. Post Category
3. Date
4. Author
5. Summary
6. Body
b. Resources > Links
1. Secondary Navigation - Categories
a. Sample Categories:
i. Local Services
ii. RDA and Drug Coverage
iii. Mental Health Resources
2. Category page
a. Include the following links in the 'Local Services' category
i. Hypertension clinics
ii. Home Care services
iii. Vaccine Clinics
c. Resources > Forms
i. Display a table with form TITLE and CATEGORY
ii. Side Navigation
1. Form Categories
a. Use the following sample Categories
i. Referrals
ii. Insurance
iii. Intake
iv. Discharge
v. Waivers
5. Alerts
a. Main page
i. List of all Alert posts
1. Include post TITLE as a link to the post
ii. Side Navigation
1. Alerts Archive
a. shown as Month + Number of posts
iii. Alerts > [Alert page]
1. Include TITLE, DATE, AUTHOR, BODY
6. Contact Us
a. Map
b. Hours of operation
c. Address
d. Phone number
e. Fax number
e. Fax number
f. Map
g. Email

Design notes:
- fixed width
- responsive (need designs for mobile, tablet, and desktop)
- simple, dark font, white background
- use Font Awesome icons where needed
- user adds own logo

Target Market(s)

Northway Clinics

Industry/Entity Type

Medical

Number of Pages Required

5+ page

Font styles to use
Serif
Sans Serif

Requirements
Must have
• Please keep designs very simple.
• Examples:
• https://www.quolbin.com/install
• http://www.ventrohax.com/company/about-us
• http://brindlequota.org/
• http://www.trosk.com/
Should not have
• Minimal or no use of shadows and gradients

```html
<!DOCTYPE html>
<html lang="en">
<head>
<meta charset="utf-8">
<title>Northway Clinics – Schedule</title>
<link href="https://fonts.googleapis.com/css2?family=Open+Sans:wght@400;600;700&family=Lato:wght@400;700&family=Raleway:wght@500&display=swap" rel="stylesheet">
<style>
:root{
  --blue:#0a8be0;
  --blue-light:#3aa9f0;
  --ink:#222;
  --text:#333;
  --muted:#888;
  --band:#f7f7f7;
  --row-alt:#f4f4f4;
  --line:#e2e2e2;
  --footer:#262626;
  --footer-text:#8a8a8a;
  --footer-head:#a9a9a9;
}
*{margin:0;padding:0;box-sizing:border-box}
html,body{width:1200px;height:698px;overflow:hidden;background:#fff}
body{font-family:"Open Sans",Arial,sans-serif;color:var(--text);position:relative}
a{color:inherit;text-decoration:none}

.topbar{position:absolute;left:0;top:0;width:1200px;height:30px;background:var(--blue);color:#fff;font-family:"Lato",sans-serif;font-size:10px}
.topbar .left{position:absolute;left:162px;top:7px}
.topbar .right{position:absolute;right:161px;top:7px}
.topbar .sep{display:inline-block;width:1px;height:14px;background:#fff;vertical-align:-3px;margin:0 5px}

.header{position:absolute;top:30px;left:0;width:1200px;height:83px}
.brand{position:absolute;left:162px;top:27px;display:flex;align-items:center;gap:12px;font-family:"Raleway",sans-serif;font-weight:500;font-size:21px;color:var(--ink)}
.brand .dot{width:12px;height:12px;border-radius:50%;background:var(--blue)}
.nav{position:absolute;left:0;top:0;width:1200px;height:83px;font-family:"Lato",sans-serif;font-size:11px;color:var(--ink)}
.nav a{position:absolute;top:0;height:83px;line-height:83px;white-space:nowrap}
.nav a.active{background:var(--blue);color:#fff;width:60px;text-align:center}

.page-head{position:absolute;top:113px;left:0;width:1200px;height:59px;background:var(--band)}
.page-head h1{position:absolute;left:162px;top:14px;font-size:10px;font-weight:700;color:var(--ink)}
.crumbs{position:absolute;left:162px;top:33px;font-size:10px;color:var(--ink)}

.sidenav{position:absolute;left:162px;top:217px;width:202px}
.sidenav h2{font-size:11px;font-weight:700;color:var(--ink);padding-bottom:4px;border-bottom:1px solid var(--line)}
.sidenav ul{list-style:none;margin-top:1px}
.sidenav li{font-size:10px;color:var(--ink);padding-left:14px;height:22.5px;line-height:22.5px}
.sidenav li.current{color:var(--blue);font-weight:700}

.schedule{position:absolute;left:386px;top:214px}
.schedule h2{font-size:14px;font-weight:700;color:var(--ink);margin-bottom:7px}
table{border-collapse:collapse;width:428px;border:1px solid var(--line);box-shadow:0 1px 2px rgba(0,0,0,.08)}
th{background:var(--blue-light);color:#fff;font-size:9px;font-weight:700;height:24px;width:43px;border-left:1px solid rgba(255,255,255,.45)}
th.name{width:128px;border-left:0}
td{height:22.5px;font-size:10px;color:var(--ink);text-align:center;border-left:1px solid var(--line)}
td.name{text-align:left;padding-left:14px;border-left:0}
tr:nth-child(even) td{background:var(--row-alt)}
.tick{width:9px;height:8px;vertical-align:middle}

.footer{position:absolute;top:455px;left:0;width:1200px;height:243px;background:var(--footer);border-top:4px solid var(--blue);color:var(--footer-text);font-size:10px}
.footer .brand{top:40px;color:#fff}
.footer .about{position:absolute;left:162px;top:85px;width:200px;font-size:9px;line-height:13.5px;color:#ddd}
.footer h3{font-size:12px;font-weight:600;color:var(--footer-head);margin-bottom:8px}
.fnav{position:absolute;left:461px;top:31px}
.fnav li{list-style:none;height:18px}
.fnav li.current{color:#ddd}
.hours{position:absolute;left:610px;top:31px}
.hours dl{display:grid;grid-template-columns:91px auto}
.hours dt,.hours dd{height:18px}
.contact{position:absolute;left:838px;top:31px}
.contact dl{display:grid;grid-template-columns:89px auto}
.contact dt,.contact dd{line-height:15px}
.bottom{position:absolute;left:0;top:202px;width:1200px;height:37px;border-top:1px solid #444;font-size:10px}
.bottom span{position:absolute;top:9px}
</style>
</head>
<body>
<svg width="0" height="0" style="position:absolute"><symbol id="tick" viewBox="0 0 10 8"><path d="M1 4.2 3.8 7 9 1.2" fill="none" stroke="#999" stroke-width="1.8" stroke-linecap="round" stroke-linejoin="round"/></symbol></svg>

<div class="topbar">
  <div class="left">To help Here : 111 480 2020<span class="sep"></span>Email : Contact@ Northway.ca</div>
  <div class="right">Book an Appointment<span class="sep"></span>Physician Toolbox</div>
</div>

<header class="header">
  <div class="brand"><span class="dot"></span>Northway Clinics</div>
  <nav class="nav">
    <a href="#" style="left:586px">Home</a>
    <a href="#" class="active" style="left:647px">Our Clinic</a>
    <a href="#" style="left:741px">Our Staff</a>
    <a href="#" style="left:824px">Resources</a>
    <a href="#" style="left:912px">Alerts</a>
    <a href="#" style="left:979px">Contact Us</a>
  </nav>
</header>

<section class="page-head">
  <h1>SCHEDULE</h1>
  <div class="crumbs">HOME / OUR CLINIC / SCHEDULE</div>
</section>

<aside class="sidenav">
  <h2>OUR CLINIC</h2>
  <ul><li>About</li><li>Misssion</li><li>Services</li><li>Policies</li><li class="current">Schedules</li></ul>
</aside>

<main class="schedule">
  <h2>SCHEDULE</h2>
  <table>
    <tr><th class="name"></th><th>MON</th><th>TUE</th><th>WED</th><th>THU</th><th>FRI</th><th>SAT</th><th>SUN</th></tr>
    <tr><td class="name">Dr. Ellen Marsh</td><td><svg class="tick"><use href="#tick"/></svg></td><td></td><td><svg class="tick"><use href="#tick"/></svg></td><td><svg class="tick"><use href="#tick"/></svg></td><td><svg class="tick"><use href="#tick"/></svg></td><td></td><td><svg class="tick"><use href="#tick"/></svg></td></tr>
    <tr><td class="name">Dr. Owen Pratt</td><td><svg class="tick"><use href="#tick"/></svg></td><td><svg class="tick"><use href="#tick"/></svg></td><td><svg class="tick"><use href="#tick"/></svg></td><td></td><td><svg class="tick"><use href="#tick"/></svg></td><td><svg class="tick"><use href="#tick"/></svg></td><td></td></tr>
    <tr><td class="name">Dr. Neil Hartog</td><td><svg class="tick"><use href="#tick"/></svg></td><td></td><td><svg class="tick"><use href="#tick"/></svg></td><td><svg class="tick"><use href="#tick"/></svg></td><td></td><td></td><td></td></tr>
    <tr><td class="name">Dr. Simon Varga</td><td></td><td><svg class="tick"><use href="#tick"/></svg></td><td></td><td><svg class="tick"><use href="#tick"/></svg></td><td></td><td></td><td></td></tr>
    <tr><td class="name">Dr. Paul Gerrin</td><td><svg class="tick"><use href="#tick"/></svg></td><td><svg class="tick"><use href="#tick"/></svg></td><td><svg class="tick"><use href="#tick"/></svg></td><td></td><td><svg class="tick"><use href="#tick"/></svg></td><td></td><td><svg class="tick"><use href="#tick"/></svg></td></tr>
  </table>
</main>

<footer class="footer">
  <div class="brand"><span class="dot"></span>Northway Clinics</div>
  <p class="about">Lorem Ipsum is simply dummy text of the printing and typesetting industry. Lorem Ipsum has been the industry's standard dummy text</p>
  <div class="fnav"><h3>Navigation</h3><ul><li class="current">Home</li><li>Our Clinic</li><li>Newsletter</li><li>Our Staff</li><li>Resources</li></ul></div>
  <div class="hours"><h3>Hours of Opration</h3>
    <dl><dt>Monday :</dt><dd>8:00 AM - 6:00 PM</dd><dt>Tuesday :</dt><dd>8:00 AM - 6:00 PM</dd><dt>Wednesday :</dt><dd>8:00 AM - 6:00 PM</dd><dt>Thursday :</dt><dd>8:00 AM - 6:00 PM</dd><dt>Friday :</dt><dd>8:00 AM - 6:00 PM</dd><dt>Saturday :</dt><dd>9:00 AM - 4:00 PM</dd><dt>Sunday :</dt><dd>9:00 AM - 4:00 PM</dd></dl></div>
  <div class="contact"><h3>Contact Us</h3>
    <dl><dt>Telephone :</dt><dd>604-555-0142</dd><dt>Email:</dt><dd>contact@northway.ca</dd><dt>Address:</dt><dd>48 Alder Street<br>&nbsp;Harbourview,B.C. Canada,<br>&nbsp;K7R 2TN</dd></dl></div>
  <div class="bottom">
    <span style="left:162px">© 2015 Northway Clinics. All Rights Reservsd</span>
    <span style="left:463px">About Us</span>
    <span style="left:530px">Terms of Use</span>
    <span style="left:615px">Privacy Policy</span>
    <span style="right:164px">Site design &amp; developed by Brightloom Web Studio</span>
  </div>
</footer>
</body>
</html>
```